Vibrant, yet professional, stationery set and other designs required.

I need to source a fantastic designer for a new project as part of my company using a new logo designed via sketch harbor.

**UPDATE** I am not looking for just 'fine' design that will suffice. I am looking for something great.

We are a life assurance brokerage based in Dublin, Ireland and BrightRoost.ie is our new website aimed at providing services for young families in Ireland. We are hoping to be the 'Velro' level of service providers in this area and I am looking for the quality of design to reflect this :-) Hopefully that makes sense!

I have a preference for straight lines over curves and waves.

I need...

1. Business card
2. Letterhead
3. Banner (for printing - 76cm X 305cm)
4. Car branding for KORVA 9 (2014 sport model) I believe the templates are freely available online.

Target Market(s)

Parents in Ireland - Aged 27 to 50.

Industry/Entity Type

Financial Planning

Colors

Designer to choose colors to be used in the design.

Requirements
Must have
• All of the items listed in the description above. I like clean, bright, legible, vibrant and professional design.
Should not have
• No silly or 'cheap' looking designs. This is a professional company looking to provide a professional service.

```html
<!DOCTYPE html>
<html lang="en">
<head>
<meta charset="utf-8">
<title>BrightRoost.ie Business Card</title>
<link rel="stylesheet" href="https://fonts.googleapis.com/css2?family=Roboto:wght@400;500;700&family=Roboto+Condensed:wght@500&display=swap">
<style>
  :root {
    --backdrop: #c4c4c4;
    --brand-orange: #f0811a;
    --card-white: #f7f7f7;
    --text-dark: #4a4a4a;
    --text-grey: #8a8f94;
    --white: #ffffff;
  }
  * { margin: 0; padding: 0; box-sizing: border-box; }
  html, body {
    width: 1200px;
    height: 960px;
    overflow: hidden;
    background: var(--backdrop);
    font-family: "Roboto", Arial, sans-serif;
  }
  .canvas { position: relative; width: 1200px; height: 960px; }

  .card { position: absolute; width: 600px; height: 340px; }

  .card-front {
    left: 320px; top: 106px;
    background: var(--brand-orange);
    display: flex; align-items: center; justify-content: center;
  }
  .wordmark-front {
    color: var(--white);
    font-weight: 700;
    font-size: 58px;
    letter-spacing: -0.5px;
    margin-top: -20px;
  }

  .card-back {
    left: 320px; top: 494px;
    background: var(--card-white);
    text-align: center;
  }
  .wordmark-back {
    position: absolute; left: 0; right: 0; top: 108px;
    color: var(--brand-orange);
    font-weight: 700;
    font-size: 24px;
  }
  .rule {
    position: absolute; left: 120px; width: 360px; height: 1px;
    background: linear-gradient(90deg, transparent, var(--brand-orange) 30%, var(--brand-orange) 70%, transparent);
  }
  .rule-top { top: 146px; }
  .rule-bottom { top: 278px; }
  .contact { position: absolute; left: 0; right: 0; top: 157px; }
  .person { line-height: 24px; }
  .person-name {
    font-family: "Roboto Condensed", "Roboto", Arial, sans-serif;
    font-weight: 500; font-size: 19px; color: var(--brand-orange);
  }
  .person-role { font-size: 14px; color: var(--text-grey); }
  .contact-line { font-size: 14px; color: var(--text-dark); line-height: 19px; }
  .contact-line.address { margin-top: 1px; margin-bottom: 5px; }
</style>
</head>
<body>
<main class="canvas">
  <section class="card card-front" aria-label="Business card front">
    <p class="wordmark-front">BrightRoost.ie</p>
  </section>

  <section class="card card-back" aria-label="Business card back">
    <p class="wordmark-back">BrightRoost.ie</p>
    <div class="rule rule-top"></div>
    <div class="contact">
      <p class="person"><span class="person-name">Ciara Doyle -</span> <span class="person-role">CEO/Founder</span></p>
      <p class="contact-line address">42 Larkfield Road, Rathmines, Dublin D06 K7P2</p>
      <p class="contact-line">P : 555 201 3847&nbsp;&nbsp;M : 555 318 7720</p>
      <p class="contact-line">F : 555 470 1296&nbsp;&nbsp;E : info@brightroost.ie</p>
      <p class="contact-line">W : www.brightroost.ie</p>
    </div>
    <div class="rule rule-bottom"></div>
  </section>
</main>
</body>
</html>
```